Brambleton Pizza Website

We are working with Brambleton Pizza and designing them a website.

Some sites to use for content/competitors and inspiration:

https://fennimores.com
https://www.bhq-eats.com
https://brightorchard.com/en-us/

Thank you for taking the time to consider designing a website for us. We are web developers based in Stockton, CA, USA. Most of our projects go through the same process. Understanding this process may help you win a project with us. We custom-code all of our websites in-house. We don’t have any requirements as to what tools you use for your design, but we prefer Figma files. For any design that we label as four-stars, we send it to the client for review. The client picks the final design they want us to use. Once we complete this process, we will continue to show additional clients all the four-star sites and purchase them later. Your designs will have multiple chances to sell. For better chances of success, we ask that you follow these guidelines.

IMAGES:
If you use any images or icons in the design, we ask that you have a link to the asset so we can purchase the image/icon. Most of the designs we submit do not have the customer’s images on them unless they have some great images. Be creative; show us the feeling you are trying to portray with your image choices. Use any royalty-free site you choose. We subscribe to Quillstone and mainly use their images, but we can purchase images outside of Quillstone.

PLEASE NOTE: we will not submit designs to clients with watermarks on the images.

FONTS:
We ask that you identify the fonts used in the design. This can be done in a message if you want. We typically use Google Fonts and Quillstone Fonts.

CONTENT:
We're always open to different content and ideas. We often submit designs with stock images so the client can see our vision. We typically take pictures after the website launch to use their images with our vision. Lorem Ipsum is fine for paragraphs, but we ask that you write the headers in correct English. We want to be able to show the vision and identify the sections of the website.

INSPIRATION:
We typically add a couple of links in the brief of websites we like to help you get started in your design.

REVISIONS:
We do not often ask for revisions of the designs unless we see something in the design that may not appeal to the client. If there are slight changes that we want to make, we do that in the development process.

FEEDBACK:
We rarely give feedback on designs during the design process. We are working on many website projects and do not have the time to provide feedback. We usually respond if your request is well thought out and asks specific questions, but a note asking “feedback, please” usually goes unanswered.

```html
<!DOCTYPE html>
<html lang="en">
<head>
<meta charset="utf-8">
<title>Brambleton Pizza</title>
<link rel="stylesheet" href="https://fonts.googleapis.com/css2?family=Oswald:wght@400;500;600;700&family=Poppins:wght@400;500;600&display=swap">
<style>
:root{
  --red:#e3262b;
  --red-dark:#b81c20;
  --green:#3c9a2e;
  --green-dark:#2c7a22;
  --ink:#1d1d1d;
  --night:#0d0d0d;
  --white:#ffffff;
  --grey:#6b6b6b;
  --line:#e2e2e2;
}
*{box-sizing:border-box;margin:0;padding:0}
html,body{width:1200px;height:3180px;overflow:hidden}
body{font-family:'Poppins',sans-serif;color:var(--ink);background:var(--white);position:relative}
.heading{font-family:'Oswald',sans-serif;text-transform:uppercase;font-weight:600}
.btn{display:inline-block;background:var(--red);color:var(--white);font-family:'Oswald',sans-serif;font-weight:500;font-size:15px;letter-spacing:.5px;padding:12px 30px;border-radius:24px;text-transform:uppercase}

.topbar{height:28px;background:var(--red);color:var(--white);text-align:center;font-family:'Oswald',sans-serif;font-size:13px;line-height:28px;letter-spacing:.6px}

.nav{height:102px;position:relative;background:var(--white)}
.nav-links{position:absolute;top:44px;display:flex;gap:34px;font-family:'Oswald',sans-serif;font-size:15px;text-transform:uppercase;font-weight:500}
.nav-left{left:110px}
.nav-left .active{color:var(--red);border-bottom:2px solid var(--red);padding-bottom:4px}
.nav-right{right:250px}
.nav-icons{position:absolute;right:110px;top:44px;display:flex;gap:22px}
.brand{position:absolute;left:50%;top:24px;transform:translateX(-50%);display:flex;align-items:center;gap:10px;font-family:'Oswald',sans-serif;font-weight:700;font-size:38px;line-height:1.2;color:var(--ink);text-transform:uppercase}
.brand-dot{width:16px;height:16px;border-radius:50%;background:var(--red);flex:none}

.hero{position:relative;height:550px;background:#151515;color:var(--white);overflow:hidden}
.hero-photo{position:absolute;right:0;top:0;width:720px;height:550px;background:radial-gradient(circle at 58% 46%,#c8582a 0,#9a3a1c 26%,#3a1a10 48%,#151515 72%)}
.hero-copy{position:absolute;left:110px;top:92px;width:560px}
.hero-kicker{color:#4bc23a;font-size:28px;font-weight:600}
.hero-title{font-size:50px;line-height:1.12;margin-top:10px;font-weight:700}
.hero-text{font-size:14px;line-height:23px;margin-top:18px;color:#e7e7e7;width:420px}
.hero .btn{margin-top:26px}
.dots{display:flex;gap:8px;margin-top:34px}
.dots span{width:10px;height:10px;border-radius:50%;background:#777}
.dots span:first-child{background:var(--white)}
.hero-curve{position:absolute;left:0;top:596px;width:1200px;height:110px}

.about{position:absolute;top:760px;left:0;width:1200px;height:560px}
.about-mark{position:absolute;left:70px;top:110px;width:460px;display:flex;align-items:center;gap:14px;justify-content:center;font-family:'Oswald',sans-serif;font-weight:700;font-size:84px;color:var(--ink);text-transform:uppercase}
.about-mark .brand-dot{width:30px;height:30px}
.about-copy{position:absolute;left:640px;top:60px;width:470px}
.about-copy h2{font-size:36px}
.about-copy h3{color:var(--green);font-size:18px;font-weight:500;margin-top:6px}
.about-copy p{font-size:14px;line-height:25px;color:var(--grey);margin-top:14px}
.about .btn{margin-top:22px}

.menu{position:absolute;top:1330px;left:0;width:1200px;height:640px}
.menu-band{position:absolute;inset:0;width:1200px;height:640px}
.menu-title{position:absolute;top:100px;width:100%;text-align:center;color:var(--white)}
.menu-title h2{font-size:42px}
.menu-title p{font-size:14px;margin-top:2px}
.dish{position:absolute;top:210px;width:260px;text-align:center}
.dish-photo{width:260px;height:260px;border-radius:50%;border:8px solid var(--white);box-shadow:0 6px 18px rgba(0,0,0,.25)}
.dish h4{color:var(--white);font-size:20px;margin-top:30px}
.arrow{position:absolute;top:326px;width:34px;height:34px;border-radius:50%;background:var(--white);display:flex;align-items:center;justify-content:center}

.specials{position:absolute;top:2060px;left:0;width:1200px;text-align:center}
.specials h2{font-size:38px}
.specials h3{color:var(--green);font-size:18px;font-weight:500;margin-top:4px}
.card{position:absolute;top:130px;width:296px;border:1px solid var(--line);background:var(--white);text-align:center}
.card-photo{height:220px}
.card h4{font-size:16px;font-weight:500;line-height:22px;margin:26px 40px 0;min-height:44px}
.card .btn{margin:18px 0 24px;font-size:13px;padding:9px 24px}

.footer-curve{position:absolute;top:2600px;left:0;width:1200px;height:90px}
.footer{position:absolute;top:2660px;left:0;width:1200px;height:520px;background:var(--night);color:var(--white)}
.footer-brand{position:absolute;left:100px;top:150px;display:flex;align-items:center;gap:12px;font-family:'Oswald',sans-serif;font-weight:700;font-size:46px;text-transform:uppercase}
.footer-col{position:absolute;top:130px}
.footer-col h5{font-family:'Oswald',sans-serif;font-size:20px;font-weight:500;margin-bottom:20px}
.contact-row{display:flex;align-items:center;gap:14px;font-size:13px;margin-bottom:20px}
.icon-circle{width:30px;height:30px;border-radius:50%;background:var(--red);display:flex;align-items:center;justify-content:center;flex:none}
.quick li{list-style:none;font-size:14px;line-height:25px}
.copyright{position:absolute;left:100px;right:100px;top:450px;border-top:1px solid #333;padding-top:18px;text-align:center;font-size:12px;color:#cfcfcf}
</style>
</head>
<body>

<div class="topbar">JOIN THE EPIC WAITLIST NOW</div>

<header class="nav">
  <nav class="nav-links nav-left"><span class="active">Home</span><span>Order</span><span>Menu</span><span>Catering</span></nav>
  <div class="brand"><span class="brand-dot"></span>Brambleton</div>
  <nav class="nav-links nav-right"><span>Reviews</span><span>Delivery</span></nav>
  <div class="nav-icons">
    <svg width="18" height="18" viewBox="0 0 18 18" fill="none" stroke="#1d1d1d" stroke-width="2"><circle cx="7.5" cy="7.5" r="5.5"/><path d="M12 12l5 5"/></svg>
    <svg width="18" height="18" viewBox="0 0 18 18" fill="#1d1d1d"><circle cx="9" cy="5" r="4"/><path d="M1 18c0-5 3.5-7 8-7s8 2 8 7z"/></svg>
    <svg width="18" height="18" viewBox="0 0 18 18" fill="none" stroke="#1d1d1d" stroke-width="2"><path d="M2 6h14l-1 11H3z"/><path d="M6 6V4a3 3 0 016 0v2"/></svg>
  </div>
</header>

<section class="hero">
  <div class="hero-photo" role="img" aria-label="Pepperoni pizza with basil, tomatoes and garlic on a dark table"></div>
  <div class="hero-copy">
    <div class="hero-kicker heading">Welcome To</div>
    <h1 class="hero-title heading">Brambleton Italian<br>Fresh Pizza</h1>
    <p class="hero-text">Excepteur sint occaecat cupidatat non proident, sunt in culpa qui officia deserunt mollit anim id est laborum.</p>
    <span class="btn">Shop Now</span>
    <div class="dots"><span></span><span></span><span></span></div>
  </div>
</section>
<svg class="hero-curve" viewBox="0 0 1200 110" preserveAspectRatio="none">
  <path d="M0 0 H1200 V30 Q600 110 0 30 Z" fill="#151515" transform="translate(0,-16)"/>
  <path d="M40 60 Q600 130 1160 60" fill="none" stroke="#e3262b" stroke-width="6"/>
</svg>

<section class="about">
  <div class="about-mark"><span class="brand-dot"></span>Brambleton</div>
  <div class="about-copy">
    <h2 class="heading">About Us</h2>
    <h3 class="heading">Italian Fresh Pizza</h3>
    <p>Lorem ipsum dolor sit amet, consectetur adipiscing elit, sed do eiusmod tempor incididunt ut labore et dolore magna aliqua. Ut enim ad minim veniam, quis nostrud exercitation ullamco laboris nisi ut aliquip ex ea commodo consequat. Duis aute irure dolor in reprehenderit in voluptate velit esse cillum dolore eu fugiat nulla pariatur. Excepteur sint occaecat cupidatat non proident, sunt in culpa qui officia deserunt mollit anim id est laborum.</p>
    <span class="btn">Read More</span>
  </div>
</section>

<section class="menu">
  <svg class="menu-band" viewBox="0 0 1200 640" preserveAspectRatio="none">
    <defs><linearGradient id="menuGreen" x1="0" y1="0" x2="0" y2="1"><stop offset="0" stop-color="#45a934"/><stop offset="1" stop-color="#2c7a22"/></linearGradient></defs>
    <path d="M0 60 Q600 -40 1200 60 V640 H0 Z" fill="url(#menuGreen)"/>
  </svg>
  <div class="menu-title"><h2 class="heading">Our Menu</h2><p>Excepteur sint occaecat cupidatat non proident</p></div>
  <div class="arrow" style="left:40px"><svg width="12" height="12" viewBox="0 0 12 12"><path d="M8 1L3 6l5 5" fill="none" stroke="#2c7a22" stroke-width="2"/></svg></div>
  <div class="arrow" style="right:40px"><svg width="12" height="12" viewBox="0 0 12 12"><path d="M4 1l5 5-5 5" fill="none" stroke="#2c7a22" stroke-width="2"/></svg></div>
  <div class="dish" style="left:130px"><div class="dish-photo" role="img" aria-label="Seafood pasta with shrimp" style="background:radial-gradient(circle,#e7a25a,#b9572c)"></div><h4 class="heading">Seafood Pasta</h4></div>
  <div class="dish" style="left:470px"><div class="dish-photo" role="img" aria-label="Pepperoni pizza" style="background:radial-gradient(circle,#d9622e,#9c3418)"></div><h4 class="heading">Pepperoni</h4></div>
  <div class="dish" style="left:810px"><div class="dish-photo" role="img" aria-label="Pasta carbonara" style="background:radial-gradient(circle,#efcf86,#c79a4a)"></div><h4 class="heading">Pasta Carbonara</h4></div>
</section>

<section class="specials">
  <h2 class="heading">Brambleton Specials</h2>
  <h3 class="heading">Italian Fresh Pizza</h3>
  <div class="card" style="left:112px"><div class="card-photo" role="img" aria-label="Whole pizza with tomatoes and basil" style="background:linear-gradient(135deg,#3a2a22,#c4572a)"></div><h4 class="heading">Take &amp; Bake Always Oven Fresh</h4><span class="btn">Read More</span></div>
  <div class="card" style="left:452px"><div class="card-photo" role="img" aria-label="Seafood pasta served on a wooden table" style="background:linear-gradient(135deg,#6b4a30,#d09050)"></div><h4 class="heading">Get Together Seafood Pasta For 4</h4><span class="btn">Read More</span></div>
  <div class="card" style="left:792px"><div class="card-photo" role="img" aria-label="Pepperoni pizza on a board" style="background:linear-gradient(135deg,#b96a3a,#e8c08a)"></div><h4 class="heading">Earn Points On Every Pepperoni</h4><span class="btn">Read More</span></div>
</section>

<svg class="footer-curve" viewBox="0 0 1200 90" preserveAspectRatio="none">
  <path d="M40 50 Q600 -20 1160 50" fill="none" stroke="#e3262b" stroke-width="6"/>
  <path d="M0 60 Q600 10 1200 60 V90 H0 Z" fill="#0d0d0d"/>
</svg>
<footer class="footer">
  <div class="footer-brand"><span class="brand-dot"></span>Brambleton</div>
  <div class="footer-col" style="left:440px">
    <h5>Contact Us</h5>
    <div class="contact-row"><span class="icon-circle"><svg width="14" height="14" viewBox="0 0 14 14" fill="#fff"><path d="M7 0a5 5 0 00-5 5c0 4 5 9 5 9s5-5 5-9a5 5 0 00-5-5zm0 7a2 2 0 110-4 2 2 0 010 4z"/></svg></span>Brambleton Pizza, Stockton CA</div>
    <div class="contact-row"><span class="icon-circle"><svg width="14" height="14" viewBox="0 0 14 14" fill="none" stroke="#fff" stroke-width="1.5"><rect x="1" y="3" width="12" height="8"/><path d="M1 3l6 5 6-5"/></svg></span>info@brambletonpizza.com</div>
    <div class="contact-row"><span class="icon-circle"><svg width="14" height="14" viewBox="0 0 14 14" fill="#fff"><path d="M3 1l2 3-1.5 1.5a8 8 0 005 5L10 9l3 2-1 2C6 13 1 8 1 2z"/></svg></span>+1000 0000 0000</div>
  </div>
  <div class="footer-col" style="left:700px">
    <h5>Quick Links</h5>
    <ul class="quick"><li>Home</li><li>About Us</li><li>Menu</li><li>Order Online</li><li>What's New</li><li>Contact Us</li></ul>
  </div>
  <div class="footer-col" style="left:950px">
    <h5>Follow Us</h5>
    <div class="contact-row"><span class="icon-circle"></span>Chatterbook</div>
    <div class="contact-row"><span class="icon-circle"></span>Snapgram</div>
  </div>
  <div class="copyright">Copyright@2024 Brambleton Pizza.All Rights Reserved</div>
</footer>

</body>
</html>
```